Business Card Design for Varomir Facility Services

We are looking for a Business Card Design for the Company "Varomir Facility Services."
Front side:
- Company Logo (small)
- Company Name, address, pohone, website and personal data.
- white background, for text e.g. company colors (blue or green like in the logo)
Please use following data:
Company data:
Varomir Facility Services Kostelac
Birkenhaldweg 14
6330 Cham
www.varomir-fs.ch
Person data:
Tarik Kostelac
Geschäftsführer
+41 76 519 47 83
info@varomir-fs.ch
Back side:
could be colored in blue or green
please use a big logo sing and some smaller icons to say what is all beeing offered in facility services, like cleaning, maintenance cleaning
industrial cleaning, caretaking, gardening, disposal. There is no need for everyone of the icons if there are similar or an icon is standing for more of them.
colors to use:
blue: HEX 246BB0
green: HEX 52B33E

```html
<!DOCTYPE html>
<html lang="de">
<head>
<meta charset="utf-8">
<title>Varomir Facility Services – Business Card</title>
<link rel="stylesheet" href="https://fonts.googleapis.com/css2?family=Roboto:wght@400;700&family=Montserrat:wght@700&display=swap">
<style>
  :root {
    --brand-blue: #246BB0;
    --deep-blue: #1456A3;
    --brand-green: #52B33E;
    --white: #ffffff;
    --stage: #e6e7e9;
  }
  * { box-sizing: border-box; margin: 0; padding: 0; }
  html, body { width: 1200px; height: 1200px; overflow: hidden; }
  body {
    background: var(--stage);
    font-family: "Roboto", Arial, sans-serif;
    display: flex;
    flex-direction: column;
    align-items: center;
    justify-content: center;
    gap: 40px;
  }
  .card {
    position: relative;
    width: 900px;
    height: 514px;
    border-radius: 34px;
    overflow: hidden;
    box-shadow: 0 10px 30px rgba(0,0,0,0.18);
  }

  /* Back side */
  .card-back {
    background: var(--brand-blue);
    color: var(--white);
    display: flex;
    flex-direction: column;
    align-items: center;
    padding-top: 70px;
  }
  .brand {
    display: flex;
    align-items: center;
    gap: 22px;
    font-family: "Montserrat", Arial, sans-serif;
    font-weight: 700;
    line-height: 1.05;
  }
  .brand-dot { border-radius: 50%; flex: none; }
  .card-back .brand { color: var(--white); font-size: 50px; }
  .card-back .brand-dot { width: 70px; height: 70px; background: var(--white); }
  .brand-name span { display: block; }
  .brand-name .brand-sub { font-size: 0.62em; letter-spacing: 0.08em; }

  .services {
    display: flex;
    gap: 56px;
    margin-top: 62px;
    list-style: none;
  }
  .service {
    display: flex;
    flex-direction: column;
    align-items: center;
    width: 120px;
    text-align: center;
  }
  .service-icon {
    width: 104px;
    height: 104px;
    border-radius: 50%;
    border: 4px solid var(--white);
    padding: 5px;
  }
  .service-icon span {
    display: block;
    width: 100%;
    height: 100%;
    border-radius: 50%;
    background: radial-gradient(circle, #ffffff 0%, #e8eef6 100%);
  }
  .service-label {
    margin-top: 10px;
    font-size: 15px;
    font-weight: 700;
    text-transform: uppercase;
    line-height: 1.1;
  }

  /* Front side */
  .card-front { background: var(--white); }
  .front-wave { position: absolute; inset: 0; width: 100%; height: 100%; }
  .card-front .brand {
    position: absolute;
    left: 60px;
    top: 56px;
    color: var(--brand-blue);
    font-size: 46px;
  }
  .card-front .brand-dot { width: 60px; height: 60px; background: var(--brand-green); }

  .website {
    position: absolute;
    left: 46px;
    bottom: 38px;
    display: flex;
    align-items: center;
    gap: 10px;
    color: var(--white);
    font-size: 20px;
  }
  .website svg { width: 22px; height: 22px; }

  .contact {
    position: absolute;
    left: 520px;
    top: 346px;
    color: var(--white);
    font-size: 17px;
    line-height: 1.25;
  }
  .person-name { font-size: 26px; font-weight: 700; line-height: 1.1; }
  .person-role { font-size: 16px; margin-bottom: 4px; }
  .company-line { color: var(--brand-green); font-weight: 700; }
  .contact-row { display: flex; align-items: center; gap: 8px; }
  .contact-row svg { width: 16px; height: 16px; flex: none; }
</style>
</head>
<body>

  <section class="card card-back" aria-label="Back side">
    <div class="brand">
      <span class="brand-dot"></span>
      <div class="brand-name">
        <span>VAROMIR</span>
        <span class="brand-sub">FACILITY SERVICES</span>
      </div>
    </div>
    <ul class="services">
      <li class="service">
        <div class="service-icon"><span role="img" aria-label="Icon: bucket and brush for maintenance cleaning"></span></div>
        <div class="service-label">Maintenance<br>Cleaning</div>
      </li>
      <li class="service">
        <div class="service-icon"><span role="img" aria-label="Icon: handshake in a heart for caretaking"></span></div>
        <div class="service-label">Caretaking</div>
      </li>
      <li class="service">
        <div class="service-icon"><span role="img" aria-label="Icon: flower in a pot for gardening"></span></div>
        <div class="service-label">Gardening</div>
      </li>
      <li class="service">
        <div class="service-icon"><span role="img" aria-label="Icon: waste bin for disposal"></span></div>
        <div class="service-label">Disposal</div>
      </li>
    </ul>
  </section>

  <section class="card card-front" aria-label="Front side">
    <svg class="front-wave" viewBox="0 0 900 514" preserveAspectRatio="none" aria-hidden="true">
      <path d="M0,200 C80,270 200,318 360,338 C220,332 90,292 0,252 Z" fill="var(--brand-green)"/>
      <path d="M0,270 C160,330 300,340 440,335 C640,325 790,250 900,150 L900,514 L0,514 Z" fill="var(--deep-blue)"/>
    </svg>

    <div class="brand">
      <span class="brand-dot"></span>
      <div class="brand-name">
        <span>VAROMIR</span>
        <span class="brand-sub">FACILITY SERVICES</span>
      </div>
    </div>

    <div class="website">
      <svg viewBox="0 0 24 24" fill="none" stroke="currentColor" stroke-width="1.6">
        <circle cx="12" cy="12" r="10"/>
        <ellipse cx="12" cy="12" rx="4.5" ry="10"/>
        <path d="M2 12h20M4 6.5h16M4 17.5h16"/>
      </svg>
      <span>www.<b>varomir-fs</b>.ch</span>
    </div>

    <div class="contact">
      <div class="person-name">Tarik Kostelac</div>
      <div class="person-role">Geschäftsführer</div>
      <div class="company-line">Varomir Facility Services Kostelac</div>
      <div>Birkenhaldweg 14</div>
      <div>6330 Cham</div>
      <div class="contact-row">
        <svg viewBox="0 0 24 24" fill="currentColor"><path d="M6.6 10.8a15.1 15.1 0 0 0 6.6 6.6l2.2-2.2c.3-.3.7-.4 1-.2 1.1.4 2.3.6 3.6.6.6 0 1 .4 1 1V20c0 .6-.4 1-1 1A17 17 0 0 1 3 4c0-.6.4-1 1-1h3.5c.6 0 1 .4 1 1 0 1.3.2 2.5.6 3.6.1.3 0 .7-.2 1z"/></svg>
        <span>+41 76 519 47 83</span>
      </div>
      <div class="contact-row">
        <svg viewBox="0 0 24 24" fill="none" stroke="currentColor" stroke-width="1.8"><rect x="3" y="5" width="18" height="14" rx="1.5"/><path d="M3 6l9 7 9-7"/></svg>
        <span>info@varomir-fs.ch</span>
      </div>
    </div>
  </section>

</body>
</html>
```